Billboard design 8x3M RAVU (Spanish company)

We´re located in the south of Spain. We run a local telecom company.
We sell Fiber optic, and mobile phone lines mainly.
The billboard will have to be in Spanish, I would like the price to be something you spot on first sight when passing by in the car.
Our company color is blue, like in our logo which I will add. I will also add a example from what we currently have.
The new offer should be:
1000 megas + 100Gigas movil con llamadas ilimitadas. (meaning 1000Mb fiber optic speed and 100Gb data and unlimited calls for 1 mobile line)
Our details are: phone line 958 47 6620
Website: ra-vu.es

```html
<!DOCTYPE html>
<html lang="es">
<head>
<meta charset="UTF-8">
<title>RAVU – Valla 8x3</title>
<link href="https://fonts.googleapis.com/css2?family=Bebas+Neue&family=Poppins:wght@500;600;800&display=swap" rel="stylesheet">
<style>
  :root {
    --page-bg: #e8e8e8;
    --blue-deep: #0a3f93;
    --blue-mid: #0f63c4;
    --blue-light: #1ea4ec;
    --yellow: #ffd500;
    --navy: #16304f;
    --white: #ffffff;
  }
  * { margin: 0; padding: 0; box-sizing: border-box; }
  html, body {
    width: 1200px; height: 571px; overflow: hidden;
    background: var(--page-bg);
  }
  .billboard {
    position: absolute; left: 76px; top: 88px;
    width: 1050px; height: 394px; overflow: hidden;
    background: linear-gradient(100deg, var(--blue-deep) 0%, var(--blue-mid) 45%, var(--blue-light) 100%);
    font-family: "Poppins", sans-serif;
    color: var(--white);
  }
  .brand { position: absolute; left: 48px; top: 80px; width: 170px; }
  .brand-name {
    font-family: "Poppins", sans-serif; font-weight: 800;
    font-size: 50px; line-height: 1; letter-spacing: 3px; color: var(--white);
  }
  .brand-tagline { font-weight: 600; font-size: 12px; margin-top: 6px; letter-spacing: .2px; }
  .headline {
    position: absolute; left: 244px; top: 50px;
    font-family: "Bebas Neue", sans-serif; font-size: 82px; line-height: .86;
  }
  .headline-top { color: var(--yellow); display: block; }
  .headline-bottom { color: var(--white); display: block; }
  .spec { position: absolute; top: 192px; text-align: left; font-weight: 800; line-height: .9; }
  .spec-number { display: block; font-size: 48px; color: var(--yellow); letter-spacing: -1px; }
  .spec-unit { display: block; font-size: 29px; color: var(--white); }
  .spec-fiber { left: 48px; }
  .spec-data { left: 204px; }
  .plus-box {
    position: absolute; left: 175px; top: 218px; width: 22px; height: 22px;
    background: var(--yellow); border-radius: 3px;
  }
  .plus-box::before, .plus-box::after {
    content: ""; position: absolute; background: var(--white);
    left: 50%; top: 50%; transform: translate(-50%, -50%);
  }
  .plus-box::before { width: 12px; height: 3px; }
  .plus-box::after { width: 3px; height: 12px; }
  .mobile-plan {
    position: absolute; left: 328px; top: 190px;
    font-family: "Bebas Neue", sans-serif; font-size: 40px; line-height: 1;
  }
  .price-tag {
    position: absolute; left: 614px; top: 192px; width: 144px; height: 66px;
    background: var(--yellow); border-radius: 10px;
    display: flex; align-items: center; justify-content: center;
    font-weight: 800; font-size: 50px; color: var(--navy); letter-spacing: -1px;
  }
  .hero-visual {
    position: absolute; left: 676px; top: 40px; width: 372px; height: 344px;
    background: radial-gradient(ellipse at 55% 45%, rgba(255,255,255,.28) 0%, rgba(80,150,230,.25) 45%, rgba(30,120,220,0) 75%);
  }
  .phone-pill {
    position: absolute; left: 0; top: 286px; width: 388px; height: 58px;
    background: var(--yellow); border-radius: 0 30px 30px 0;
    display: flex; align-items: center; padding-left: 47px; gap: 12px;
  }
  .phone-icon { width: 30px; height: 30px; flex: none; }
  .phone-number { font-weight: 800; font-size: 41px; color: var(--navy); letter-spacing: -.5px; }
  .website {
    position: absolute; left: 404px; top: 296px;
    font-weight: 500; font-size: 33px; color: var(--white);
  }
</style>
</head>
<body>
  <main class="billboard">
    <div class="brand">
      <div class="brand-name">RAVU</div>
      <div class="brand-tagline">Wifi | Fibra | Movil | Tv</div>
    </div>

    <h1 class="headline">
      <span class="headline-top">TU FIBRA + MÓVIL</span>
      <span class="headline-bottom">AL MEJOR PRECIO</span>
    </h1>

    <div class="spec spec-fiber">
      <span class="spec-number">1000</span>
      <span class="spec-unit">MEGAS</span>
    </div>
    <div class="plus-box" aria-hidden="true"></div>
    <div class="spec spec-data">
      <span class="spec-number">100</span>
      <span class="spec-unit">GIGAS</span>
    </div>

    <p class="mobile-plan">MOVIL CON<br>LLAMADAS ILIMITADAS</p>

    <div class="price-tag">35€</div>

    <div class="hero-visual" role="img" aria-label="Cohete saliendo de la pantalla de un portátil y cable de fibra con hilos de cobre"></div>

    <div class="phone-pill">
      <svg class="phone-icon" viewBox="0 0 30 30" aria-hidden="true">
        <circle cx="15" cy="15" r="15" fill="#ffffff"/>
        <path d="M11.2 8.5c.5-.4 1.2-.3 1.5.3l1.2 2.3c.3.5.1 1.1-.3 1.4l-.9.7c.6 1.4 1.7 2.6 3.1 3.3l.8-.8c.4-.4 1-.5 1.4-.2l2.2 1.3c.5.3.7 1 .3 1.5l-.9 1.2c-.5.6-1.3.9-2.1.7-3.7-1-6.6-3.9-7.6-7.6-.2-.8.1-1.6.7-2.1z" fill="#16304f"/>
        <path d="M16.5 9.2a4.5 4.5 0 0 1 4.3 4.3M16.5 6.8a7 7 0 0 1 6.7 6.7" stroke="#16304f" stroke-width="1.3" fill="none" stroke-linecap="round"/>
      </svg>
      <span class="phone-number">958 47 6620</span>
    </div>

    <div class="website">www.ra-vu.es</div>
  </main>
</body>
</html>
```